BOLD & MINIMALIST DESIGN NEEDED

We want a very bold but minimalistic business card design that is impactful and utilizes both sides of the business card. Our current logo is included for your use.

We want bold fonts and good use of negative space. We don't want the logo to overpower the design.

Target Market(s)

Professionals who are building new commercial buildings.

Industry/Entity Type

Construction

Contact Information for Business Card

Name, Title, email, office phone, cell phone, website

Font styles to use
Serif
Sans Serif

Requirements
Must have
• Bold design!

```html
<!DOCTYPE html>
<html lang="en">
<head>
<meta charset="utf-8">
<title>Ridgeline Design + Build — Business Card</title>
<link href="https://fonts.googleapis.com/css2?family=Roboto:wght@400;500;700;900&display=swap" rel="stylesheet">
<style>
  :root {
    --stage: #2b2b2b;
    --card-white: #ffffff;
    --card-black: #161616;
    --pattern-top: #2a2a2a;
    --pattern-bottom: #111111;
    --green: #7dc126;
    --ink: #111111;
    --muted: #3c3c3c;
    --rule: #4a4a4a;
  }
  * { margin: 0; padding: 0; box-sizing: border-box; }
  html, body { width: 1200px; height: 900px; overflow: hidden; }
  body {
    background: var(--stage);
    font-family: "Roboto", Arial, sans-serif;
    display: flex;
    flex-direction: column;
    align-items: center;
    justify-content: center;
    gap: 40px;
  }
  .card {
    width: 700px;
    height: 400px;
    border-radius: 28px;
    position: relative;
    overflow: hidden;
  }

  /* Back side */
  .card-back { background: var(--card-black); }
  .back-pattern {
    position: absolute; inset: 0;
    background: linear-gradient(160deg, var(--pattern-top), var(--pattern-bottom));
  }
  .back-mark {
    position: absolute; left: 50%; top: 50%;
    transform: translate(-50%, -50%);
    display: flex; align-items: center; gap: 10px;
    color: var(--card-white);
    font-weight: 900; font-size: 22px; letter-spacing: 1px;
    text-transform: uppercase;
  }
  .mark-dot { width: 14px; height: 14px; border-radius: 50%; background: var(--green); }

  /* Front side */
  .card-front { background: var(--card-white); }
  .brand {
    position: absolute; left: 50px; top: 110px; width: 330px; height: 150px;
    display: flex; align-items: center; gap: 14px;
  }
  .brand-dot { width: 26px; height: 26px; border-radius: 50%; background: var(--green); flex: none; }
  .brand-name {
    color: var(--ink); font-weight: 900; font-size: 34px; line-height: 1.05;
    text-transform: uppercase;
  }
  .divider {
    position: absolute; left: 400px; top: 48px; width: 1.5px; height: 196px;
    background: var(--rule);
  }
  .contact { position: absolute; left: 428px; top: 40px; }
  .person-name { color: var(--green); font-weight: 700; font-size: 30px; }
  .person-title { color: var(--muted); font-size: 17px; margin: 4px 0 14px 24px; }
  .contact-list { list-style: none; }
  .contact-list li {
    display: flex; align-items: center; gap: 12px;
    font-size: 17px; color: var(--ink); height: 30px; white-space: nowrap;
  }
  .icon {
    width: 22px; height: 22px; border-radius: 50%; background: var(--green);
    display: flex; align-items: center; justify-content: center; flex: none;
  }
  .address-band {
    position: absolute; left: 0; right: 0; top: 272px; height: 62px;
    background: var(--green);
    display: flex; align-items: center; justify-content: center; gap: 12px;
    color: var(--card-white); font-size: 20px; white-space: nowrap;
  }
</style>
</head>
<body>

  <section class="card card-back" aria-label="Card back">
    <div class="back-pattern" role="img" aria-label="Repeating embossed brand pattern on black"></div>
    <div class="back-mark"><span class="mark-dot"></span>Ridgeline</div>
  </section>

  <section class="card card-front" aria-label="Card front">
    <div class="brand">
      <span class="brand-dot"></span>
      <span class="brand-name">Ridgeline<br>Design + Build</span>
    </div>

    <div class="divider"></div>

    <div class="contact">
      <h1 class="person-name">Daniel Harper</h1>
      <p class="person-title">Owner</p>
      <ul class="contact-list">
        <li>
          <span class="icon"><svg width="12" height="12" viewBox="0 0 24 24"><path fill="#111" d="M6.6 10.8a15 15 0 0 0 6.6 6.6l2.2-2.2c.3-.3.7-.4 1-.2 1.1.4 2.3.6 3.6.6.6 0 1 .4 1 1V20c0 .6-.4 1-1 1A17 17 0 0 1 3 4c0-.6.4-1 1-1h3.5c.6 0 1 .4 1 1 0 1.3.2 2.5.6 3.6.1.3 0 .7-.2 1z"/></svg></span>
          044-555 210 384
        </li>
        <li>
          <span class="icon"><svg width="12" height="12" viewBox="0 0 24 24"><path fill="#111" d="M3 8c3-3 15-3 18 0v3h-5V9H8v2H3zm3 5h12l2 7H4zm6 2a2 2 0 1 0 0 4 2 2 0 0 0 0-4z"/></svg></span>
          044-555 210 397
        </li>
        <li>
          <span class="icon"><svg width="12" height="12" viewBox="0 0 24 24"><path fill="#111" d="M2 5h20v14H2zm2 2v.5l8 5 8-5V7l-8 5z"/></svg></span>
          info@ridgelinedb.com
        </li>
        <li>
          <span class="icon"><svg width="12" height="12" viewBox="0 0 24 24"><circle cx="12" cy="12" r="9" fill="none" stroke="#111" stroke-width="2"/><path d="M3 12h18M12 3c3 3 3 15 0 18M12 3c-3 3-3 15 0 18" fill="none" stroke="#111" stroke-width="1.6"/></svg></span>
          www.ridgelinedb.com
        </li>
      </ul>
    </div>

    <div class="address-band">
      <svg width="18" height="24" viewBox="0 0 24 32" aria-hidden="true"><path fill="#fff" d="M12 0a11 11 0 0 0-11 11c0 8 11 21 11 21s11-13 11-21A11 11 0 0 0 12 0zm0 15a4 4 0 1 1 0-8 4 4 0 0 1 0 8z"/></svg>
      18 Quarry Road, Northfield 45310, Eastland
    </div>
  </section>

</body>
</html>
```